Full re-design of visual identity

We have just re-designed our logo and would like to apply it on our folders, business cards, stationery, and etc... we are attaching new logo + the material we need to re-design... we will provide full corel draw files to help make job easier and also because lot of icons and artwork can be still used...

any doubts we are at your disposal. thanks in advance.

```html
<!DOCTYPE html>
<html lang="en">
<head>
<meta charset="utf-8">
<title>Corivo – DL Envelope Stationery</title>
<link rel="stylesheet" href="https://fonts.googleapis.com/css2?family=Open+Sans:wght@400;600;700&display=swap">
<style>
  :root {
    --page-bg: #f4f4f4;
    --paper: #ffffff;
    --paper-edge: #e2e2e2;
    --brand-grey: #6d6e71;
    --text-grey: #58595b;
    --brand-orange: #e8712f;
    --window-fill: #f3f4f5;
    --window-edge: #d9dadc;
    --flap-line: #e6e6e6;
  }
  * { box-sizing: border-box; margin: 0; padding: 0; }
  html, body { width: 1200px; height: 1000px; overflow: hidden; }
  body {
    background: var(--page-bg);
    font-family: "Open Sans", Arial, sans-serif;
    color: var(--text-grey);
    position: relative;
  }
  .envelope {
    position: absolute;
    left: 220px;
    width: 760px;
    height: 380px;
    background: var(--paper);
    border: 1px solid var(--paper-edge);
    box-shadow: 0 6px 18px rgba(0,0,0,0.06);
    overflow: hidden;
  }
  .envelope--back { top: 60px; }
  .envelope--front { top: 540px; }

  /* back side */
  .flap-line {
    position: absolute;
    left: 0; top: 0;
    width: 760px; height: 380px;
  }
  .back-brand {
    position: absolute;
    right: 34px;
    bottom: 150px;
    text-align: right;
  }

  /* brand lockup */
  .brand {
    display: inline-flex;
    align-items: center;
    gap: 5px;
  }
  .brand__name {
    font-weight: 700;
    font-size: 26px;
    letter-spacing: -0.5px;
    color: var(--brand-grey);
    line-height: 1;
  }
  .brand__dot {
    width: 10px; height: 10px;
    border-radius: 50%;
    background: var(--brand-orange);
  }
  .brand__tagline {
    display: block;
    font-size: 6px;
    letter-spacing: 1.5px;
    color: var(--brand-grey);
    text-transform: uppercase;
    margin-top: 3px;
  }

  /* front side */
  .edge-band {
    position: absolute;
    left: 0; top: 0;
    width: 22px; height: 100%;
  }
  .edge-band__grey { height: 62%; background: var(--brand-grey); }
  .edge-band__orange { height: 38%; background: var(--brand-orange); }

  .address-window {
    position: absolute;
    left: 450px; top: 70px;
    width: 270px; height: 120px;
    background: var(--window-fill);
    border: 1px solid var(--window-edge);
    border-radius: 4px;
  }

  .sender {
    position: absolute;
    left: 46px;
    bottom: 40px;
  }
  .sender .brand__name { font-size: 22px; }
  .sender__rule {
    width: 88px; height: 2px;
    background: var(--brand-orange);
    margin: 6px 0 8px;
  }
  .contact-list { list-style: none; }
  .contact-list li {
    display: flex;
    align-items: flex-start;
    gap: 7px;
    font-size: 10px;
    line-height: 1.35;
    margin-bottom: 3px;
  }
  .contact-list svg {
    flex: none;
    width: 10px; height: 10px;
    margin-top: 2px;
    fill: var(--brand-orange);
  }
</style>
</head>
<body>

  <section class="envelope envelope--back" aria-label="Envelope back">
    <svg class="flap-line" viewBox="0 0 760 380" aria-hidden="true">
      <path d="M0 78 L10 88 L738 88 L760 70" fill="none" stroke="var(--flap-line)" stroke-width="1.5"/>
    </svg>
    <div class="back-brand">
      <span class="brand">
        <span class="brand__name">Corivo</span>
        <span class="brand__dot"></span>
      </span>
      <span class="brand__tagline">connect · grow · deliver</span>
    </div>
  </section>

  <section class="envelope envelope--front" aria-label="Envelope front">
    <div class="edge-band">
      <div class="edge-band__grey"></div>
      <div class="edge-band__orange"></div>
    </div>

    <div class="address-window"></div>

    <div class="sender">
      <span class="brand">
        <span class="brand__name">Corivo</span>
        <span class="brand__dot"></span>
      </span>
      <div class="sender__rule"></div>
      <ul class="contact-list">
        <li>
          <svg viewBox="0 0 10 10" aria-hidden="true"><path d="M5 0a3.5 3.5 0 0 0-3.5 3.5C1.5 6 5 10 5 10s3.5-4 3.5-6.5A3.5 3.5 0 0 0 5 0zm0 5a1.4 1.4 0 1 1 0-2.8A1.4 1.4 0 0 1 5 5z"/></svg>
          <span>48 Harbor Lane, Millbrook,<br>20417, Westland</span>
        </li>
        <li>
          <svg viewBox="0 0 10 10" aria-hidden="true"><path d="M2 0.5l2 2.2-1 1.2c.6 1.3 1.6 2.3 2.9 2.9l1.2-1 2.2 2-1 1.7C4.3 9.5.5 5.7.3 1.5z"/></svg>
          <span>555-0192-38</span>
        </li>
        <li>
          <svg viewBox="0 0 10 10" aria-hidden="true"><rect x="1" y="2" width="8" height="6" rx="1"/></svg>
          <span>555-0192-39</span>
        </li>
        <li>
          <svg viewBox="0 0 10 10" aria-hidden="true"><path d="M0.5 2h9v6h-9z M0.5 2l4.5 3.5L9.5 2" stroke="#fff" stroke-width="0.8"/></svg>
          <span>hello@corivo-mail.com</span>
        </li>
        <li>
          <svg viewBox="0 0 10 10" aria-hidden="true"><circle cx="5" cy="5" r="4.5"/><path d="M0.5 5h9M5 0.5c-2 2.5-2 6.5 0 9M5 0.5c2 2.5 2 6.5 0 9" stroke="#fff" stroke-width="0.7" fill="none"/></svg>
          <span>www.corivo-studio.com</span>
        </li>
      </ul>
    </div>
  </section>

</body>
</html>
```